Menükarte für Weingastronomie
Zielgruppe
Wir betreiben einen eigenen Weinberg und stellen unseren eigenen Wein her - die Website ist gerade im Umbau https://orva.hosting.brelnetdienste.de/
Zielgruppe sind Weinliebhaber - für den Vertrieb bieten wir unseren Wein jetzt auch in der gehobenen Gastronomie.
Der Auftakt in der Gastronomie wird eine große Vertikal-Probe mit all unseren Jahrgängen, Menübegleitung und unserem Winzer sein.
Dafür soll es Tisch-Sets in DIN A3 geben.
Aufgabenstellung
BITTE DIE Platzierung der Gläser und der Teller beachten, so dass diese Platz haben. Zumindest die Weingläser mit deren 'Platzhalter' sollten in dem oberen Bereich angesiedelt sein. Sie Anlage/Datei.
Es soll eine historische Moselkarte als Grafik mit berücksichtigt werden - in Dateiupload enthalten.
Der Grundton des Sets soll grau sein, so ähnlich wie das Logo vom Restaurant (HORB - in Dateiupload enthalten)
ORVA Logo (unser Logo - ebenfalls in Dateiupload enthalten)

```html
<!DOCTYPE html>
<html lang="de">
<head>
<meta charset="utf-8">
<title>Tisch-Set Vertikal Probe – ORVA Riesling 2011 – 2022</title>
<link rel="stylesheet" href="https://fonts.googleapis.com/css2?family=Open+Sans:wght@400;700&family=Crimson+Text:wght@400&display=swap">
<style>
  :root {
    --stage: #25272b;
    --paper: #ece4d5;
    --paper-edge: #ddd3c1;
    --concrete-light: #b4b4b3;
    --concrete-dark: #9b9b9a;
    --disc: #55575a;
    --disc-ring: #efe6d6;
    --dots: #f4f1ea;
    --ink: #4f5052;
    --ink-soft: #6b6b6b;
    --tag: #bcd6c0;
    --tag-dark: #5d7f6a;
    --map-frame: #8c877c;
    --map-green: #c9d6bd;
    --map-cream: #efe7d6;
    --white: #ffffff;
  }
  * { margin: 0; padding: 0; box-sizing: border-box; }
  html, body {
    width: 1200px;
    height: 3000px;
    overflow: hidden;
    background: var(--stage);
  }
  .placemat {
    position: absolute;
    left: 50px;
    top: 1100px;
    width: 1100px;
    height: 799px;
    background: var(--paper);
    overflow: hidden;
    font-family: "Open Sans", sans-serif;
  }
  .placemat__header {
    position: absolute;
    left: 0; top: 0;
    width: 100%;
    height: 55px;
    background: var(--paper);
    display: flex;
    align-items: center;
  }
  .restaurant-name {
    position: absolute;
    left: 19px;
    font-weight: 700;
    font-size: 24px;
    letter-spacing: 3px;
    color: var(--ink);
  }
  .event-title {
    position: absolute;
    left: 159px;
    font-family: "Crimson Text", serif;
    font-size: 28px;
    color: var(--ink);
  }
  .event-subtitle {
    position: absolute;
    left: 373px;
    font-size: 19px;
    letter-spacing: 5px;
    color: var(--ink-soft);
  }
  .glass-zone {
    position: absolute;
    left: 0; top: 55px;
    width: 100%;
    height: 405px;
    background:
      radial-gradient(ellipse at 30% 20%, rgba(255,255,255,0.18), transparent 60%),
      radial-gradient(ellipse at 80% 80%, rgba(0,0,0,0.08), transparent 55%),
      linear-gradient(180deg, var(--concrete-light), var(--concrete-dark));
  }
  .glass-spot {
    position: absolute;
    width: 216px;
    height: 216px;
    margin-left: -108px;
    margin-top: -108px;
    border-radius: 50%;
    background: var(--disc);
    border: 7px solid var(--disc-ring);
    color: var(--white);
    font-weight: 700;
    font-size: 14px;
    text-align: center;
  }
  .glass-spot::before {
    content: "";
    position: absolute;
    inset: 8px;
    border-radius: 50%;
    border: 3px dotted var(--dots);
  }
  .glass-spot__label {
    position: absolute;
    left: 0; width: 100%;
    top: 30px;
    line-height: 18px;
  }
  .glass-spot__years {
    position: absolute;
    left: 0; width: 100%;
    top: 66px;
    list-style: none;
    line-height: 18px;
  }
  .glass-spot--single .glass-spot__label { top: 42px; }
  .glass-spot--single .glass-spot__years { top: 84px; }
  .glass-spot--one { left: 136px; top: 123px; }
  .glass-spot--two { left: 432px; top: 123px; }
  .glass-spot--three { left: 680px; top: 123px; }

  .winery-tag {
    position: absolute;
    left: 803px; top: 0;
    width: 95px; height: 157px;
    background: var(--tag);
    box-shadow: 2px 3px 6px rgba(0,0,0,0.25);
    text-align: center;
  }
  .winery-tag__name {
    margin-top: 14px;
    font-family: "Crimson Text", serif;
    font-size: 34px;
    line-height: 1;
    color: var(--tag-dark);
  }
  .winery-tag__mark {
    width: 36px; height: 36px;
    margin: 34px auto 0;
    background: var(--tag-dark);
  }

  .map-band {
    position: absolute;
    left: 0; top: 460px;
    width: 100%;
    height: 339px;
    background: var(--paper-edge);
    padding: 8px;
  }
  .map-band__frame {
    width: 100%;
    height: 100%;
    border: 4px double var(--map-frame);
    background:
      linear-gradient(90deg, transparent 0 46%, rgba(0,0,0,0.04) 46% 46.3%, transparent 46.3%),
      radial-gradient(ellipse at 20% 40%, var(--map-green), transparent 45%),
      radial-gradient(ellipse at 60% 60%, var(--map-green), transparent 40%),
      radial-gradient(ellipse at 85% 35%, var(--map-green), transparent 40%),
      radial-gradient(ellipse at 45% 75%, rgba(184,154,120,0.35), transparent 35%),
      var(--map-cream);
  }
</style>
</head>
<body>
  <main class="placemat">
    <header class="placemat__header">
      <span class="restaurant-name">HORB</span>
      <span class="event-title">Vertikal Probe</span>
      <span class="event-subtitle">ORVA RIESLING 2011 - 2022</span>
    </header>

    <section class="glass-zone" aria-label="Platzierung der Weingläser">
      <div class="glass-spot glass-spot--single glass-spot--one">
        <div class="glass-spot__label">ORVA</div>
        <ul class="glass-spot__years"><li>2022</li></ul>
      </div>
      <div class="glass-spot glass-spot--two">
        <div class="glass-spot__label">ORVA</div>
        <ul class="glass-spot__years">
          <li>2021</li><li>2019</li><li>2017</li><li>2015</li><li>2013</li><li>2011</li>
        </ul>
      </div>
      <div class="glass-spot glass-spot--three">
        <div class="glass-spot__label">ORVA</div>
        <ul class="glass-spot__years">
          <li>2020</li><li>2018</li><li>2016</li><li>2014</li><li>2012</li><li>2011</li>
        </ul>
      </div>
    </section>

    <div class="winery-tag">
      <div class="winery-tag__name">ORVA</div>
      <div class="winery-tag__mark"></div>
    </div>

    <section class="map-band">
      <div class="map-band__frame" role="img" aria-label="Historische Weinbaukarte von Saar und Mosel mit dem gewundenen Flusslauf, Wäldern und Weinlagen"></div>
    </section>
  </main>
</body>
</html>
```